Lone Star Wetland Flora Stewardship Guild

We need to design the home page of this new website. We would like a fun website design for provides as a resource for members and information for potential members.
Please design so that we can see a portion of background on each side on the website.
I just need the final design files psd no coding needed.
Attached is their logo (colors are not 100% set in stone either so can mess with those as I did in the quick mockup attached)
Attached is a pdf newsletter they send out, you can get a feel for them and what they are about. The design is crappy and we are here to fix that going forward and we are starting with the website.
Here are some quick example websites (design style is open)
- I attached a quick mockup i did just for a content visual but by all means do what you want.
- http://www.brightpathleaders.example/
- http://www.civicunityhub.example/
- http://preview.webskinvault.example/show.php?cat=layouts&host=skinbazaar&temp=novaline
- http://www.meadowkeep.example/
- http://www.urbangleaners.example/
- http://www.projectcozyknit.example/
here are some of the other chapters website (pretty bad!)
and here are some of the others:
- http://www.dwrvcs.example/
- http://kwfg.example/
- http://www.blvcg.example/
Content Items that need to be included:
1. Logo
2. Menu - home, about, members, resources, events, membership, contact
3. Become a member - button or action
4. social links - chatterloop, workweave, clipstream
5. banner - that needs to explain their purpose "Promoting environmental stewardship through operations, research, education and outreach" (or this can be worked into the design)
6. Upcoming event (s)
7. Advertisement - members can place an ad on the website, this can be a placeholder for now
8. newsletter signup
9. advertise with us - this link can be in the footer
30-60 years of age, succesfull (household budgets of 120K+ men and women that live in texas.
Education

```html
<!DOCTYPE html>
<html lang="en">
<head>
<meta charset="utf-8">
<title>Lone Star Wetland Flora Stewardship Guild</title>
<link rel="stylesheet" href="https://fonts.googleapis.com/css2?family=Nunito+Sans:wght@400;600;700;800&family=Open+Sans:wght@400;600&family=Roboto+Condensed:wght@400;700&display=swap">
<style>
:root{
  --red:#d92b2e;
  --red-dark:#b81f22;
  --navy:#1f4a86;
  --navy-deep:#163866;
  --blue-btn:#2563a8;
  --orange:#e9573a;
  --gray-text:#5a5a5a;
  --line:#dcdcdc;
  --white:#ffffff;
  --yellow:#f6b81d;
}
*{box-sizing:border-box;margin:0;padding:0}
html,body{width:1175px;height:1200px;overflow:hidden}
body{position:relative;font-family:"Open Sans",sans-serif;background:#cfe0ee}
.page-backdrop{position:absolute;inset:0;background:linear-gradient(180deg,#bcd4ec 0%,#dbe7f1 30%,#6f9a62 48%,#8aa9b6 62%,#6b8a7f 78%,#9aa85a 100%)}
.site{position:absolute;left:122px;top:0;width:929px;height:1200px}
.social{position:absolute;left:4px;top:56px;display:flex;gap:6px}
.social a{display:flex;align-items:center;gap:4px;height:24px;padding:0 8px 0 4px;border-radius:12px;background:var(--navy-deep);color:var(--white);font:600 11px "Nunito Sans",sans-serif;text-decoration:none}
.social a::before{content:"";width:10px;height:10px;border-radius:50%;background:var(--white)}
.join-btn{position:absolute;left:756px;top:55px;width:174px;height:33px;background:var(--blue-btn);color:var(--white);font:600 14px "Nunito Sans",sans-serif;display:flex;align-items:center;padding-left:12px;gap:8px;clip-path:polygon(0 0,92% 0,100% 50%,92% 100%,0 100%)}
.content{position:absolute;left:0;top:98px;width:929px;height:1102px;background:var(--white)}
.nav{position:absolute;left:0;top:0;width:929px;height:50px;background:linear-gradient(180deg,var(--red),var(--red-dark));font:600 16px "Nunito Sans",sans-serif;color:var(--white)}
.nav ul{list-style:none;display:flex;gap:25px;position:absolute;top:16px}
.nav .left{left:33px}
.nav .right{right:23px}
.brand{position:absolute;left:50%;transform:translateX(-50%);top:0;height:50px;display:flex;align-items:center;gap:8px;font:800 30px "Nunito Sans",sans-serif;color:var(--white);white-space:nowrap}
.brand::before{content:"";width:14px;height:14px;border-radius:50%;background:var(--white)}
.brand-tag{position:absolute;left:0;top:56px;width:929px;text-align:center;font:700 9.5px "Nunito Sans",sans-serif;color:#111}
.hero{position:absolute;left:0;top:50px;width:929px;height:399px;background:linear-gradient(180deg,#c9dcee 0%,#e4ecf2 14%,#7fa24a 18%,#a7b95a 28%,#5e8fc6 40%,#8fb4db 55%,#6c9a47 70%,#8c9b3c 100%)}
.hero-caption{position:absolute;left:169px;top:116px;width:587px;text-align:center;font-family:"Nunito Sans",sans-serif;color:var(--white)}
.hero-caption .top{background:var(--orange);padding:11px 0 8px;font-size:25px;line-height:29px;font-weight:600}
.hero-caption .bottom{background:var(--navy-deep);height:40px;line-height:40px;font-size:22px;font-weight:600}
.dots{position:absolute;left:431px;top:371px;display:flex;gap:4px}
.dots span{width:14px;height:14px;border-radius:50%;background:var(--white)}
.about{position:absolute;left:40px;top:484px;width:850px;text-align:center}
.about h2{font:400 29px "Nunito Sans",sans-serif;color:var(--navy);margin-bottom:10px}
.about p{font-size:12.2px;line-height:18px;color:var(--gray-text)}
.divider{position:absolute;left:32px;top:618px;width:866px;height:1px;background:var(--line)}
.events h3{position:absolute;left:34px;top:652px;font:400 23px "Nunito Sans",sans-serif;color:var(--red)}
.event{position:absolute;width:280px;display:flex;gap:11px}
.event .thumb{width:87px;height:73px;flex:none}
.event .text{width:176px}
.event h4{font:400 14.5px "Nunito Sans",sans-serif;color:#555;margin-top:-2px;margin-bottom:4px}
.event p{font-size:11.3px;line-height:18.5px;color:var(--gray-text)}
.event a{display:inline-flex;align-items:center;gap:4px;font-size:12.5px;color:var(--navy);text-decoration:none;margin-top:2px}
.event a::after{content:"";border-left:6px solid var(--navy);border-top:5px solid transparent;border-bottom:5px solid transparent}
.ad{position:absolute;left:646px;top:665px;width:254px;height:253px;border:2px solid var(--navy);background:linear-gradient(180deg,#f8d25a,#f5b21a 75%);font-family:"Roboto Condensed",sans-serif;color:var(--white);padding:14px 8px 0 8px;text-shadow:0 1px 2px rgba(0,0,0,.45)}
.ad .hook{font-size:17px;line-height:18px;font-style:italic}
.ad .hook em{color:var(--navy-deep);text-shadow:none}
.ad .product{text-align:center;font-size:34px;color:#3a3a3a;text-shadow:none;margin-top:6px;line-height:36px}
.ad .slogan{text-align:center;font-size:10px;color:#3a3a3a;text-shadow:none;letter-spacing:.5px}
.ad .offer{font-size:17px;line-height:19px;margin-top:10px}
.ad .cta{position:absolute;left:0;bottom:0;width:100%;height:38px;background:linear-gradient(180deg,#3f69aa,var(--navy-deep));text-align:center;line-height:38px;font-size:21px}
.footer{position:absolute;left:0;top:988px;width:929px;height:114px;background:linear-gradient(180deg,#2b5b94,var(--navy-deep));color:var(--white)}
.footer-nav{position:absolute;left:47px;top:29px;font:400 14px "Nunito Sans",sans-serif}
.footer-nav span{margin:0 5px}
.copyright{position:absolute;left:47px;top:55px;font-size:12px;color:#a9bcd6}
.newsletter{position:absolute;left:696px;top:21px;width:194px}
.newsletter label{font:400 14px "Nunito Sans",sans-serif;display:block;margin-bottom:6px}
.newsletter .field{display:flex;height:24px}
.newsletter .input{flex:1;background:#5b7ea9;font-size:10px;line-height:24px;padding-left:11px}
.newsletter .submit{width:24px;background:var(--yellow);display:flex;align-items:center;justify-content:center}
.newsletter .submit::after{content:"";border-left:6px solid var(--white);border-top:5px solid transparent;border-bottom:5px solid transparent}
.advertise{position:absolute;left:796px;top:78px;font:400 13px "Nunito Sans",sans-serif;color:var(--white)}
</style>
</head>
<body>
<div class="page-backdrop" role="img" aria-label="Wetland backdrop with sky, pond water and floating lily pads"></div>
<div class="site">
  <nav class="social" aria-label="Social links">
    <a href="#">chatterloop</a><a href="#">clipstream</a><a href="#">workweave</a>
  </nav>
  <div class="join-btn">
    <svg width="16" height="16" viewBox="0 0 16 16"><circle cx="8" cy="4.5" r="3.5" fill="#fff"/><path d="M1 16c0-5 3-7 7-7s7 2 7 7z" fill="#fff"/></svg>
    Become a Member
  </div>
  <main class="content">
    <section class="hero" role="img" aria-label="Photo of a calm river winding through green wetland grasses">
      <div class="hero-caption">
        <div class="top">PROMOTING ENVIRONMENTAL STEWARDSHIP<br>THROUGH OPERATIONS,</div>
        <div class="bottom">RESEARCH, EDUCATION AND OUTREACH</div>
      </div>
      <div class="dots"><span></span><span></span><span></span><span></span></div>
    </section>
    <header class="nav">
      <ul class="left"><li>HOME</li><li>ABOUT</li><li>MEMBERS</li><li>EVENT</li></ul>
      <div class="brand">LSWFSG</div>
      <ul class="right"><li>RESOURCES</li><li>MEMBERSHIP</li><li>CONTACT</li></ul>
    </header>
    <div class="brand-tag">Lone Star Wetland Flora Stewardship Guild</div>
    <section class="about">
      <h2>Little About Our Company</h2>
      <p>Suspendisse vulputate aliquam dui Nulla elementum dui ut augue Aliquam vehicula mi at mauris Maecenas placerat nisl at consequat rhoncus sem nunc gravida justo quis eleifend arcu velit quis lacus Morbi magna magna tincidunt a mattis non imperdiet vitae tellus Sed odio est auctor ac sollicitudin in consequat vitae orci Fusce id felis Vivamus sollicitudin metus eget eros</p>
    </section>
    <div class="divider"></div>
    <section class="events">
      <h3>Upcoming Events</h3>
      <article class="event" style="left:35px;top:699px">
        <div class="thumb" role="img" aria-label="Pond with pink lily flowers" style="background:linear-gradient(135deg,#5a7f8f,#c884a8 50%,#37505a)"></div>
        <div class="text"><h4>Event Tittle goes here</h4><p>aliquam dui Nulla elementum dui ut augue Aliquam vehicula mi at mauris Maecenas placerat</p><a href="#">Read More</a></div>
      </article>
      <article class="event" style="left:334px;top:699px">
        <div class="thumb" role="img" aria-label="Dense green water hyacinth leaves" style="background:linear-gradient(135deg,#1f6a2a,#58a83a 50%,#184a20)"></div>
        <div class="text"><h4>Event Tittle goes here</h4><p>aliquam dui Nulla elementum dui ut augue Aliquam vehicula mi at mauris Maecenas placerat</p><a href="#">Read More</a></div>
      </article>
      <article class="event" style="left:35px;top:823px">
        <div class="thumb" role="img" aria-label="Close-up of a lotus flower seed pod" style="background:linear-gradient(135deg,#f2d8d8,#f1c433 50%,#d98aa0)"></div>
        <div class="text"><h4>Event Tittle goes here</h4><p>aliquam dui Nulla elementum dui ut augue Aliquam vehicula mi at mauris Maecenas placerat</p><a href="#">Read More</a></div>
      </article>
      <article class="event" style="left:334px;top:823px">
        <div class="thumb" role="img" aria-label="Underwater grass growing in a dark stream" style="background:linear-gradient(135deg,#1c2a14,#4f7a2c 55%,#2a3a1a)"></div>
        <div class="text"><h4>Event Tittle goes here</h4><p>aliquam dui Nulla elementum dui ut augue Aliquam vehicula mi at mauris Maecenas placerat</p><a href="#">Read More</a></div>
      </article>
    </section>
    <aside class="ad" aria-label="Member advertisement">
      <p class="hook">Juggling <em>spreadsheets</em> for every <em>chapter</em> meeting?<br>Keep the <em>whole program in one place</em> with...</p>
      <p class="product">AGENDO</p>
      <p class="slogan">PLAN. SHARE. ATTEND.</p>
      <p class="offer">The event planner our members rely on for the NFEO Yearly Meeting &amp; Trade Show</p>
      <p class="cta">Try agendo.example now!</p>
    </aside>
    <footer class="footer">
      <div class="footer-nav">Home<span>|</span>About<span>|</span>Members<span>|</span>Resources<span>|</span>Events<span>|</span>Membership<span>|</span>Contact</div>
      <div class="copyright">© 2014 Company Name &nbsp;All right reserved &nbsp;Term of Use</div>
      <div class="newsletter">
        <label>Newsletter Subscribe</label>
        <div class="field"><div class="input">Email address</div><div class="submit"></div></div>
      </div>
      <div class="advertise">advertise with us</div>
    </footer>
  </main>
</div>
</body>
</html>
```